new service company in the field of construction seeks to make the Creation of a PPT

We need a PPT format with a cover page a frame for presentation. our company is based in Paris which was named VORENTIX. we just did our logo attached. Our company offers services to manage and control documents that pass on projects in construction (building, infrastructure, energy, oil and gas etc. ..). We use internet systems to help us, design must show insurance, quality, and safety. Customers should build any type of works and can not build without the approved documents. These documents go through multiple validations, and vorentix staff seconded on projects, coordinate these processes and documents, quality documents, to ensure that project deadlines are met and project management sees his project developed within the period, through regular reporting. the services offered by our company help ensure the project of building on time, to ensure the project manager visibility on what e will not, and can act accordingly.

Target Market(s)

general contractor of engineering construction or big business masters lumber wholesale real estate investor, project ownership in the construction sector

Industry/Entity Type

Construction

Contact Information for Business Card

carte rectangulaire petite taille (4X6cm env)
horizontale ou verticale
prendre en compte les éléments suivants :
logo
nom de société
adresse postale (4 lignes)
teléphone:
mail
role (ex : directeur)
in the back : La qualité documentaire de vos projets

Font styles to use
Sans Serif

Colors
34a7d7
85cae6
cee9f5
0592cd

Requirements
Must have
• The project should have 2 sliders: slider 1. Cover Page 2. slider for the content of presentations THE GOAL IS TO HAVE A VISUAL IDENTITY ON PPT, MY BUSINESS CARDS AND LETTERS must stay in mind and colors of the logo that joined the design must be clean and recall the seriousness, ease. the design must take into account the page numbers Tag line: the documentary quality of your projects information such as tagline and writes must be modifiable
Nice to have
• would require the presentation of the figure shows concepts or reporting table THE GOAL IS TO HAVE A VISUAL IDENTITY ON PPT, MY BUSINESS CARDS AND LETTERS
Should not have
• not to building or building in the logo

```html
<!DOCTYPE html>
<html lang="en">
<head>
<meta charset="utf-8">
<title>VORENTIX presentation templates</title>
<link rel="stylesheet" href="https://fonts.googleapis.com/css2?family=Cabin:wght@400;500;600&display=swap">
<style>
  :root {
    --board: #c4cbce;
    --divider: #8e9598;
    --brand-blue: #215ea8;
    --brand-blue-flat: #2775b0;
    --brand-blue-light: #3f93cc;
    --brand-blue-soft: #7099cd;
    --paper: #ffffff;
    --ink-grey: #5b5f63;
    --muted-grey: #9a9ea2;
  }
  * { box-sizing: border-box; margin: 0; padding: 0; }
  html, body { width: 1200px; height: 1200px; overflow: hidden; }
  body {
    position: relative;
    background: var(--board);
    font-family: "Cabin", sans-serif;
  }
  .board-divider {
    position: absolute; left: 608px; top: 0; width: 5px; height: 1200px;
    background: var(--divider);
  }
  .slide {
    position: absolute; width: 464px; height: 261px;
    background: var(--paper); overflow: hidden;
    box-shadow: 1px 2px 4px rgba(0,0,0,.25);
  }
  .col-left { left: 85px; }
  .col-right { left: 670px; }
  .row-cover { top: 92px; }
  .row-content { top: 402px; }
  .row-closing { top: 713px; }

  .abs { position: absolute; }
  .brand-name {
    position: absolute; font-weight: 600; color: var(--brand-blue);
    letter-spacing: .02em; line-height: 1; text-transform: uppercase;
  }

  /* Cover A */
  .cover-a .cover-band { left: 0; top: 168px; width: 464px; height: 93px; background: var(--brand-blue); }
  .cover-a .cover-disc {
    left: 249px; top: 24px; width: 184px; height: 184px; border-radius: 50%;
    background: var(--brand-blue); border: 8px solid var(--paper);
  }
  .cover-a .brand-name { left: 134px; top: 141px; font-size: 22px; }
  .cover-title { font-size: 14px; line-height: 1; }
  .cover-date { font-size: 8px; line-height: 1; }
  .cover-a .cover-title { left: 26px; top: 208px; color: var(--paper); }
  .cover-a .cover-date { left: 26px; top: 226px; color: #c9d7ea; }
  .cover-a .cover-rule { left: 26px; top: 240px; width: 200px; height: 1px; background: #9fb7d8; }

  /* Cover B */
  .cover-b .cover-panel {
    left: 245px; top: 0; width: 201px; height: 261px;
    background: linear-gradient(180deg, var(--brand-blue-light), var(--brand-blue));
  }
  .cover-b .cover-disc {
    left: 306px; top: 74px; width: 80px; height: 80px; border-radius: 50%;
    background: var(--paper); box-shadow: 2px 2px 4px rgba(0,0,0,.3);
  }
  .cover-b .brand-name { right: 233px; top: 15px; font-size: 22px; }
  .cover-b .cover-title { left: 26px; top: 208px; color: var(--ink-grey); }
  .cover-b .cover-date { left: 26px; top: 226px; color: var(--muted-grey); }
  .cover-b .cover-rule { left: 26px; top: 240px; width: 200px; height: 2px; background: var(--brand-blue); }

  /* Content slides */
  .content-header { left: 0; top: 0; width: 464px; height: 52px; background: var(--brand-blue); }
  .content-slide.gradient .content-header {
    background: linear-gradient(180deg, var(--brand-blue-light), var(--brand-blue) 60%);
  }
  .content-title { left: 26px; top: 16px; font-size: 16px; line-height: 1; color: var(--paper); }
  .content-subtitle { left: 26px; top: 35px; font-size: 10px; line-height: 1; color: #d4e0ef; }
  .content-slide .header-disc { border-radius: 50%; background: var(--paper); }
  .content-slide.flat .header-disc { left: 408px; top: -2px; width: 56px; height: 56px; }
  .content-slide.gradient .header-disc { left: 406px; top: 8px; width: 36px; height: 36px; }
  .content-slide .brand-name { left: 26px; top: 235px; font-size: 16px; }
  .page-number {
    left: 418px; top: 239px; font-size: 9px; line-height: 1; color: var(--ink-grey);
    padding-right: 4px; border-right: 1px solid var(--ink-grey); border-radius: 0 8px 8px 0;
  }

  /* Closing slides */
  .closing-slide { text-align: center; }
  .closing-slide.flat { background: var(--brand-blue-flat); }
  .closing-slide.gradient { background: linear-gradient(180deg, var(--brand-blue-light), var(--brand-blue)); }
  .closing-slide .brand-name { left: 0; width: 464px; top: 28px; font-size: 40px; color: var(--paper); }
  .closing-slide .closing-disc {
    left: 187px; top: 70px; width: 90px; height: 90px; border-radius: 50%; background: var(--paper);
  }
  .closing-tagline { left: 0; width: 464px; top: 213px; font-size: 14px; line-height: 1; color: var(--paper); }
</style>
</head>
<body>
  <div class="board-divider"></div>

  <section class="slide cover-a col-left row-cover">
    <div class="abs cover-band"></div>
    <div class="abs cover-disc"></div>
    <div class="brand-name">VORENTIX</div>
    <div class="abs cover-title">Lorem ipsum dolor sit amet</div>
    <div class="abs cover-date">Date</div>
    <div class="abs cover-rule"></div>
  </section>

  <section class="slide cover-b col-right row-cover">
    <div class="abs cover-panel"></div>
    <div class="abs cover-disc"></div>
    <div class="brand-name">VORENTIX</div>
    <div class="abs cover-title">Lorem ipsum dolor sit amet</div>
    <div class="abs cover-date">Date</div>
    <div class="abs cover-rule"></div>
  </section>

  <section class="slide content-slide flat col-left row-content">
    <div class="abs content-header"></div>
    <div class="abs content-title">Lorem ipsum dolor sit amet</div>
    <div class="abs content-subtitle">Lorem ipsum dolor sit amet</div>
    <div class="abs header-disc"></div>
    <div class="brand-name">VORENTIX</div>
    <div class="abs page-number">22</div>
  </section>

  <section class="slide content-slide gradient col-right row-content">
    <div class="abs content-header"></div>
    <div class="abs content-title">Lorem ipsum dolor sit amet</div>
    <div class="abs content-subtitle">Lorem ipsum dolor sit amet</div>
    <div class="abs header-disc"></div>
    <div class="brand-name">VORENTIX</div>
    <div class="abs page-number">22</div>
  </section>

  <section class="slide closing-slide flat col-left row-closing">
    <div class="brand-name">VORENTIX</div>
    <div class="abs closing-disc"></div>
    <div class="abs closing-tagline">Lorem ipsum dolor</div>
  </section>

  <section class="slide closing-slide gradient col-right row-closing">
    <div class="brand-name">VORENTIX</div>
    <div class="abs closing-disc"></div>
    <div class="abs closing-tagline">Lorem ipsum dolor</div>
  </section>
</body>
</html>
```